I have a logo and need to design the business card and stationery.
Updates

The uploaded logo image named as GREYMARSH CONSTRUCTION which is to be replaced to GREYMARSH CONTRACTS. Kindly add below details and submit the designs- Company name- Greymarsh Engineering Contracts LLP Name & Post- Kelvan Joshi (Designated Partner) Address- Block No.317, Wing C, Tulvo Trade Court, Manek Pural Road, Ruparel Industrial Estate, Goregaon(E), Mumbai - 400 063 Contact- +91 97415 60382 Email- kelvanjoshi@mailbrook.example Website- www.greymarshcontracts.example Contact for Letterhead- +91-22-28754193

Hi Tovin Rahul, We are liking your Design #28860835. We have suggested some changes which are mentioned in feedback. Kindly revert with it asap to finalize this design.

Colors

Designer to choose colors to be used in the design.

```html
<!DOCTYPE html>
<html lang="en">
<head>
<meta charset="utf-8">
<title>Greymarsh Contracts – Stationery</title>
<link href="https://fonts.googleapis.com/css2?family=Open+Sans:wght@400;600;700&family=Poppins:wght@500;600&display=swap" rel="stylesheet">
<style>
  :root{
    --bg:#d9d9d9;
    --paper:#ffffff;
    --ink:#2b2b2b;
    --text:#555555;
    --rule:#8a8a8a;
    --dark-card:#333333;
    --band:#2e2e2e;
  }
  *{box-sizing:border-box;margin:0;padding:0}
  html,body{width:1200px;height:930px;overflow:hidden}
  body{background:var(--bg);font-family:"Open Sans",sans-serif;color:var(--text);position:relative}

  /* Letterhead */
  .letterhead{position:absolute;left:104px;top:120px;width:530px;height:678px;background:var(--paper);box-shadow:0 2px 8px rgba(0,0,0,.15);overflow:hidden}
  .side-band{position:absolute;left:0;top:0;width:26px;height:100%;background:var(--band)}
  .brand{position:absolute;display:flex;align-items:center;gap:8px;color:var(--ink);font-weight:700;line-height:1.05}
  .brand-square{width:26px;height:26px;border:4px solid var(--ink);flex:none}
  .letterhead .brand{left:50%;top:40px;transform:translateX(-50%);font-size:17px;letter-spacing:1px}
  .letter-body{position:absolute;left:50px;top:121px;width:428px;font-size:8.6px;line-height:15.2px}
  .letter-body .date{margin-bottom:12px}
  .letter-body .recipient{margin-bottom:33px;line-height:10.2px}
  .letter-body .greeting{margin-bottom:15px}
  .letter-body p.para{text-align:justify;margin-bottom:15px}
  .closing{margin-top:26px}
  .signature{width:120px;height:14px;margin:10px 0 6px;background:linear-gradient(90deg,#e4e4e4,#f2f2f2)}
  .signer{font-size:10.5px;color:var(--ink);font-weight:600;line-height:14px}
  .letter-footer{position:absolute;left:50px;top:636px;width:432px;border-top:1px solid var(--rule);padding-top:10px;display:flex;justify-content:space-between;font-size:8.8px;color:var(--ink);white-space:nowrap}
  .contact{display:flex;align-items:center;gap:4px}
  .icon-box{width:17px;height:14px;background:var(--ink);display:flex;align-items:center;justify-content:center;flex:none}

  /* Business card front */
  .card{position:absolute;left:768px;width:306px;height:176px;box-shadow:2px 2px 3px rgba(0,0,0,.45)}
  .card-front{top:401px;background:var(--paper)}
  .card-front .side-band{width:15px}
  .card-front .brand{left:14px;top:88px;transform:rotate(-90deg);transform-origin:center;font-size:10.5px;width:110px;justify-content:center;flex-direction:row}
  .card-front .brand-square{width:18px;height:18px;border-width:3px}
  .card-divider{position:absolute;left:101px;top:33px;width:1px;height:110px;background:var(--rule)}
  .card-details{position:absolute;left:110px;top:30px;color:var(--ink);font-size:8.3px;line-height:10.4px}
  .person{font-family:"Poppins",sans-serif;font-weight:600;font-size:13px;line-height:14px}
  .role{margin-bottom:10px}
  .company{font-weight:600;font-size:8.8px;line-height:11px}
  .address{margin-bottom:9px}
  .card-contact{display:flex;align-items:center;gap:4px}

  /* Business card back */
  .card-back{top:623px;background:var(--dark-card);color:#fff}
  .card-back .brand{left:50%;top:54px;transform:translateX(-50%);color:#fff;font-size:15px;letter-spacing:1px}
  .card-back .brand-square{border-color:#fff}
  .card-back .web{position:absolute;left:0;right:0;top:150px;text-align:center;font-size:7.6px}
</style>
</head>
<body>

<section class="letterhead">
  <div class="side-band" role="img" aria-label="Decorative vertical band of repeated monogram pattern"></div>
  <div class="brand"><span class="brand-square"></span><span>GREYMARSH<br>CONTRACTS</span></div>

  <div class="letter-body">
    <p class="date">Issuing Date: May 5, 2018</p>
    <p class="recipient">Name Of Employee Mr. XYZABC<br>Address of Employee<br>Address Line 2 etc..</p>
    <p class="greeting">Dear Mr.XYZABC</p>
    <p class="para">Lorem Ipsum has been the industry's standard dummy text ever since the 1500s, when an unknown printer took a galley of type and scrambled it to make a type specimen book. It has survived not only five centuries, but also the leap into electronic typesetting, remaining essentially unchanged. It was popularised in the 1960s with the release of Transfeld sheets containing Lorem Ipsum passages, and more recently with desktop publishing software like Paginor Layout including versions of Lorem Ipsum.</p>
    <p class="para">Lorem Ipsum is simply dummy text of the printing and typesetting industry. Lorem Ipsum has been the industry's standard dummy text ever since the 1500s, when an unknown printer took a galley of type and scrambled it to make a type specimen book.</p>
    <p class="para">It has survived not only five centuries, but also the leap into electronic typesetting, remaining essentially unchanged. It was popularised in the 1960s with the release of Transfeld sheets containing Lorem IpsumIpsum passages.</p>
    <p class="closing">Yours Sincerely</p>
    <div class="signature" role="img" aria-label="Handwritten signature of Marlen Oduya"></div>
    <p class="signer">Marlen Oduya</p>
    <p>Managing Director</p>
  </div>

  <footer class="letter-footer">
    <span class="contact"><span class="icon-box"><svg width="10" height="9" viewBox="0 0 10 9"><path d="M1 3 Q5 0 9 3 L8 4 L6.5 3 L3.5 3 L2 4Z M2.5 5 H7.5 V8 H2.5Z" fill="#fff"/></svg></span>+91-22-28754193</span>
    <span class="contact"><span class="icon-box"><svg width="10" height="8" viewBox="0 0 10 8"><rect x=".5" y=".5" width="9" height="7" fill="none" stroke="#fff"/><path d="M.5 .5 L5 4.5 L9.5 .5" fill="none" stroke="#fff"/></svg></span>kelvanjoshi@mailbrook.example</span>
    <span class="contact"><span class="icon-box"><svg width="9" height="9" viewBox="0 0 9 9"><circle cx="4.5" cy="4.5" r="4" fill="#fff"/></svg></span>www.greymarshcontracts.example</span>
  </footer>
</section>

<section class="card card-front">
  <div class="side-band" role="img" aria-label="Decorative vertical band of repeated monogram pattern"></div>
  <div class="brand"><span class="brand-square"></span><span>GREYMARSH CONTRACTS</span></div>
  <div class="card-divider"></div>
  <div class="card-details">
    <p class="person">Kelvan Joshi</p>
    <p class="role">Designated Partner</p>
    <p class="company">Greymarsh Engineering Contracts LLP</p>
    <p class="address">Block No.317, Wing C, Tulvo Trade Court<br>Manek Pural Road, Ruparel Industrial Estate<br>Goregaon(E), Mumbai - 400 063</p>
    <p class="card-contact"><svg width="8" height="8" viewBox="0 0 8 8"><rect x=".5" y=".5" width="7" height="7" fill="none" stroke="#2b2b2b"/><path d="M2 2 Q2 6 6 6 L6 5 L5 4.5 L4.5 5 Q3 4.5 3 3 L3.5 2.5 L3 2Z" fill="#2b2b2b"/></svg>+91 97415 60382</p>
    <p class="card-contact"><svg width="8" height="7" viewBox="0 0 8 7"><rect x="0" y="0" width="8" height="7" fill="#2b2b2b"/><path d="M0 0 L4 4 L8 0" fill="none" stroke="#fff" stroke-width=".8"/></svg>kelvanjoshi@mailbrook.example</p>
    <p class="card-contact"><svg width="8" height="8" viewBox="0 0 8 8"><circle cx="4" cy="4" r="3.5" fill="none" stroke="#2b2b2b" stroke-width=".8"/><ellipse cx="4" cy="4" rx="1.5" ry="3.5" fill="none" stroke="#2b2b2b" stroke-width=".6"/><path d="M.5 4 H7.5" stroke="#2b2b2b" stroke-width=".6"/></svg>www.greymarshcontracts.example</p>
  </div>
</section>

<section class="card card-back">
  <div class="brand"><span class="brand-square"></span><span>GREYMARSH<br>CONTRACTS</span></div>
  <p class="web">www.greymarshcontracts.example</p>
</section>

</body>
</html>
```